Existing Website Requiring new Pages

I have an existing word press website that was built using elementor.
Website: www.tallowcrestcare.com.au
I require the Vacancies page (https://www.tallowcrestcare.com.au/vacancies/) to be modified to display our new properties along with minor tweaks to how the information is presented.
The vacancies to be displayed are the exactly the same as those that are located on the homepage of QMR website (https://qmr.org.au/)
The new pages that link off the Vacancies tab will require custom design.
There are roughly 8 pages/properties to be incorporated. i wish for the design to be very similar to that displayed in the following link; https://www.polunda.com.au/vacancies/merrylands
Along with this the back end has not been updated for the last 3 years so it also requires some maintenance.
Website is in the disability industry and the custom pages will display information relative to Property Vacancies.
I have attached a ZIP file with some design guides, the information for each of the properties (which will need to be modified to show our business name Tallowcrest Care) and the example of how it is to look based off the Polunda website.
If you guys have any suggestions or ideas on how to make this more presentable or possible i'm open to your ideas.
Target Market(s)
People looking for SDA properties custom built for people with a disability
Industry/Entity Type
Disability
Coding
Coded - Design and coding required
Number of Pages Required
5+ page

```html
<!DOCTYPE html>
<html lang="en">
<head>
<meta charset="utf-8">
<title>Tallowcrest Care – Vacancies</title>
<link rel="stylesheet" href="https://fonts.googleapis.com/css2?family=Fira+Sans:wght@400;500;600&family=Arimo:wght@400;700&display=swap">
<style>
:root{
  --teal:#109b8f;
  --teal-dark:#0b7f75;
  --mint:#acdcd6;
  --orange:#fbb03b;
  --sand:#f8c56d;
  --search:#f7a21b;
  --ink:#1e1e1e;
  --grey:#555;
  --line:#d9d9d9;
  --white:#fff;
}
*{box-sizing:border-box;margin:0;padding:0}
html,body{width:1200px;height:3666px;overflow:hidden;background:var(--white)}
body{font-family:"Arimo",Arial,sans-serif;color:var(--ink)}
.page{position:relative;width:1200px;height:3666px;overflow:hidden}
.abs{position:absolute}
.head-font{font-family:"Fira Sans",Arial,sans-serif}

/* header */
.site-header{position:absolute;left:0;top:0;width:1200px;height:100px;background:var(--white);box-shadow:0 2px 6px rgba(0,0,0,.08);z-index:2}
.brand{position:absolute;left:40px;top:30px;display:flex;align-items:center;gap:8px;font-family:"Fira Sans",sans-serif;font-size:17px;color:var(--teal)}
.brand i{width:14px;height:14px;border-radius:50%;background:var(--teal);display:block}
.nav a{position:absolute;top:40px;font-family:"Fira Sans",sans-serif;font-size:19px;color:var(--teal);text-decoration:none}
.nav a.current{text-decoration:underline;text-underline-offset:4px}
.search-box{position:absolute;left:911px;top:36px;width:137px;height:30px;border:1.5px solid var(--teal);border-radius:6px}
.search-box span{position:absolute;right:5px;top:5px;width:18px;height:18px;border:1.5px solid #777;border-radius:3px}
.btn-contact{position:absolute;left:1065px;top:36px;width:102px;height:31px;border-radius:6px;background:var(--teal);color:#fff;font-family:"Fira Sans",sans-serif;font-size:16px;text-align:center;line-height:31px}

/* hero */
.hero{position:absolute;left:0;top:100px;width:1200px;height:480px}
.hero h1{position:absolute;left:68px;top:76px;font-family:"Fira Sans",sans-serif;font-weight:600;font-size:51px;color:#fff}
.hero .tagline{position:absolute;left:68px;top:135px;font-family:"Fira Sans",sans-serif;font-size:33px;color:#fff}
.hero .intro{position:absolute;left:68px;top:198px;width:495px;font-size:12px;line-height:16px;color:#fff}
.hero .cta{position:absolute;left:68px;top:300px;width:147px;height:50px;border-radius:6px;background:var(--orange);color:#fff;font-family:"Fira Sans",sans-serif;font-size:25px;line-height:50px;text-align:center}

/* provide */
.provide-title{position:absolute;left:68px;top:632px;font-family:"Fira Sans",sans-serif;font-weight:600;font-size:28px}
.provide-sub{position:absolute;left:68px;top:665px;font-family:"Fira Sans",sans-serif;font-size:25px;line-height:32px}
.photo{position:absolute}
.feature-card{position:absolute;left:561px;top:638px;width:580px;height:159px;border:1.5px solid var(--teal);border-radius:6px;background:#fff;box-shadow:0 3px 6px rgba(0,0,0,.12)}
.feature-card h3{position:absolute;left:190px;top:24px;font-size:17px;font-weight:400}
.feature-card p{position:absolute;left:190px;top:56px;width:370px;font-size:13px;line-height:17px;color:var(--grey)}
.svc{position:absolute;width:282px;height:60px;border:1.5px solid var(--teal);border-radius:5px;background:#fff;box-shadow:0 3px 5px rgba(0,0,0,.12)}
.svc svg.ico{position:absolute;left:8px;top:7px;width:46px;height:46px}
.svc p{position:absolute;left:70px;top:50%;transform:translateY(-50%);width:182px;font-size:13px;line-height:17px}
.svc .go{position:absolute;right:10px;bottom:6px;width:22px;height:22px;border:1.5px solid #333;border-radius:50%}
.svc .go::after{content:"";position:absolute;left:5px;top:6px;width:6px;height:6px;border-top:1.5px solid #333;border-right:1.5px solid #333;transform:rotate(45deg)}

/* vacancies */
.section-title{position:absolute;left:0;width:1200px;text-align:center;font-family:"Fira Sans",sans-serif;font-weight:500;font-size:30px}
.vacancy-panel{position:absolute;left:46px;top:1423px;width:1104px;height:855px;border-radius:20px;background:var(--mint)}
.vacancy-panel h2{position:absolute;left:38px;top:26px;font-family:"Fira Sans",sans-serif;font-weight:400;font-size:30px}
.vacancy-panel .lead{position:absolute;left:38px;top:76px;width:510px;font-size:16px;line-height:21px;color:#333}
.amenity{position:absolute;display:flex;align-items:center;gap:10px;font-size:13px;line-height:17px;color:#333}
.amenity svg{width:56px;height:56px;flex:none}
.lifestyle-label{position:absolute;left:37px;top:610px;font-size:15px}
.enquiry-card{position:absolute;left:594px;top:26px;width:470px;height:665px;border-radius:12px;background:#fff}
.field{position:absolute;height:54px;border:1.5px solid var(--teal);border-radius:3px;background:#fff;font-family:"Fira Sans",sans-serif;font-size:19px;color:#333;padding-left:16px;line-height:52px}
.field .chev{position:absolute;right:14px;top:14px;width:24px;height:24px;border-radius:50%;background:var(--teal)}
.field .chev::after{content:"";position:absolute;left:8px;top:5px;width:7px;height:7px;border-right:2px solid #fff;border-bottom:2px solid #fff;transform:rotate(45deg)}
.btn-teal{position:absolute;border-radius:6px;background:var(--teal);color:#fff;font-family:"Fira Sans",sans-serif;text-align:center}
.reach{position:absolute;left:32px;top:550px;font-family:"Fira Sans",sans-serif;font-size:25px;color:var(--teal)}
.contact-line{position:absolute;left:32px;display:flex;align-items:center;gap:10px;font-size:18px;color:var(--teal)}
.contact-line svg{width:26px;height:26px}
.next-steps{position:absolute;left:602px;top:715px;width:470px;font-size:15px;line-height:20px;color:#222}
.next-steps u{text-underline-offset:2px}

/* listings */
.listings{position:absolute;left:0;top:2296px;width:1200px;height:594px;background:var(--sand)}
.listings h2{position:absolute;left:21px;top:44px;font-family:"Fira Sans",sans-serif;font-weight:600;font-size:19px}
.listings .sub{position:absolute;left:24px;top:73px;width:360px;font-size:11px;line-height:14px}
.filter{position:absolute;left:640px;top:34px;width:530px;height:83px;border-radius:6px;background:#fff;box-shadow:0 2px 5px rgba(0,0,0,.12)}
.filter label{position:absolute;top:10px;font-size:12px}
.select{position:absolute;top:30px;height:41px;border:1px solid var(--line);border-radius:5px;font-size:11px;color:#666;padding-left:12px;line-height:40px}
.select::after{content:"";position:absolute;right:8px;top:11px;width:16px;height:16px;border:1px solid #777;border-radius:50%}
.search-btn{position:absolute;left:473px;top:30px;width:41px;height:41px;border-radius:4px;background:var(--search)}
.prop{position:absolute;top:149px;width:204px;height:371px;background:#fff}
.prop .pic{height:139px}
.prop h3{padding:8px 8px 0;font-family:"Fira Sans",sans-serif;font-weight:400;font-size:15px;line-height:20px}
.prop p{padding:4px 8px 0;font-size:10px;line-height:13px;color:#444}
.prop .meta{position:absolute;left:8px;top:274px;width:190px;display:grid;grid-template-columns:1fr 1fr;row-gap:8px;font-size:9px;line-height:11px;color:#444}
.prop .meta span{display:flex;align-items:center;gap:4px}
.prop .meta b{width:14px;height:14px;border:1.5px solid var(--search);border-radius:3px;flex:none}
.prop .stats{position:absolute;left:8px;bottom:10px;width:188px;display:flex;justify-content:space-between;font-size:11px}
.prop .stats b{display:inline-block;width:20px;height:12px;border:1.5px solid var(--search);border-radius:2px;vertical-align:middle}
.map{position:absolute;left:665px;top:149px;width:505px;height:371px}
.pager{position:absolute;left:427px;top:546px;display:flex;align-items:center;gap:14px;font-family:"Fira Sans",sans-serif;font-size:20px}
.pager .arrow{width:22px;height:22px;border:1.5px solid #333;border-radius:50%}
.pager .dim{color:#d9a04a}

/* help */
.help h2{position:absolute;left:33px;top:3200px;font-family:"Fira Sans",sans-serif;font-weight:600;font-size:19px}
.help p{position:absolute;left:30px;top:3244px;width:640px;font-family:"Fira Sans",sans-serif;font-size:18px;line-height:25px;color:#333}
.help-form{position:absolute;left:702px;top:2921px;width:471px;height:457px;border-radius:12px;background:var(--mint);box-shadow:0 2px 6px rgba(0,0,0,.1)}
.help-form .field{border-color:#555;font-size:18px}
.help-form .small{font-family:"Arimo",sans-serif;font-size:12px;line-height:15px;padding:8px;}

/* footer */
.site-footer{position:absolute;left:0;top:3445px;width:1200px;height:221px;background:var(--teal);color:#fff}
.footer-tab{position:absolute;left:747px;top:0;width:453px;height:43px;background:#fff;border-bottom-left-radius:30px}
.footer-tab .item{position:absolute;top:8px;text-align:right;font-size:11px;line-height:13px;color:var(--teal)}
.footer-brand{position:absolute;left:57px;top:58px;display:flex;align-items:center;gap:8px;font-family:"Fira Sans",sans-serif;font-size:19px;color:#fff}
.footer-brand i{width:14px;height:14px;border-radius:50%;background:#fff}
.socials{position:absolute;left:40px;top:131px;display:flex;gap:15px}
.socials span{width:30px;height:30px;border-radius:50%;background:#fff}
.foot-col{position:absolute;top:38px;font-size:12px;line-height:15.5px}
.foot-col h4{font-size:12px;font-weight:400;margin-bottom:8px}
.foot-col li{list-style:none}
.foot-col li::before{content:"· ";}
.foot-col a{color:#fff}
.sub-title{position:absolute;left:1001px;top:67px;font-size:12px;font-weight:700}
.sub-input{position:absolute;left:880px;top:104px;width:191px;height:38px;border-radius:5px;background:#fff;color:#888;font-size:12px;line-height:38px;padding-left:18px}
.sub-btn{position:absolute;left:1085px;top:104px;width:85px;height:38px;border-radius:5px;background:#fff;color:var(--teal);font-size:15px;line-height:38px;text-align:center}
.copyright{position:absolute;left:34px;top:181px;font-size:12px;font-weight:700}
.legal{position:absolute;right:22px;top:181px;font-size:12px;display:flex;gap:14px}
</style>
</head>
<body>
<div class="page">

<header class="site-header">
  <div class="brand"><i></i>Tallowcrest Care</div>
  <nav class="nav">
    <a class="current" style="left:185px">Home</a>
    <a style="left:282px">About</a>
    <a style="left:374px">What we do</a>
    <a style="left:507px">Referrals</a>
    <a style="left:633px">Feedback</a>
  </nav>
  <div class="search-box"><span></span></div>
  <div class="btn-contact">Contact US</div>
</header>

<section class="hero">
  <svg class="abs" style="left:0;top:0" width="1200" height="480" viewBox="0 0 1200 480">
    <path d="M0 0H1200V470H0Z" fill="var(--teal)"/>
    <path d="M0 470 L0 478 C300 472 600 470 900 472 L900 470Z" fill="#0d8a80"/>
    <ellipse cx="1150" cy="440" rx="490" ry="330" fill="#fff"/>
  </svg>
  <div class="abs" role="img" aria-label="Photo of a support worker and two young people, one using a wheelchair, reviewing notes together" style="left:676px;top:35px;width:470px;height:420px;border-radius:40% 40% 10px 10px;background:linear-gradient(160deg,#cfd8e0,#8ea4b8 55%,#3d4b5c)"></div>
  <h1>Tallowcrest Care</h1>
  <div class="tagline">Tallowcrest for an empowered future</div>
  <p class="intro">Tallowcrest Care is a Sydney based disability support services provider. Focusing on intellectual, physical &amp; sensory disabilities including mental health within the Greater Sydney region, we strive to assist our participants in leading an independent and fulfilling life.</p>
  <div class="cta">Contact Us</div>
</section>

<section class="provide">
  <h2 class="provide-title">WHAT WE PROVIDE</h2>
  <p class="provide-sub">A Quick look at Tallowcrest Care’s<br>Registration Groups</p>
  <div class="photo" style="left:95px;top:860px;width:407px;height:440px;background:var(--teal)"></div>
  <div class="photo" role="img" aria-label="Photo of three smiling women embracing" style="left:63px;top:764px;width:410px;height:491px;background:linear-gradient(135deg,#e9ddd0,#c79c86 45%,#6b4a3e)"></div>

  <div class="feature-card">
    <svg class="abs" style="left:14px;top:8px" width="142" height="142" viewBox="0 0 142 142"><circle cx="71" cy="71" r="71" fill="var(--teal)"/><circle cx="71" cy="68" r="32" fill="none" stroke="#fff" stroke-width="6"/><circle cx="71" cy="68" r="20" fill="none" stroke="#fff" stroke-width="5"/><path d="M66 98 L71 108 L76 98" fill="var(--teal)" stroke="#fff" stroke-width="5"/></svg>
    <h3>High intensity daily personal activities</h3>
    <p>Lorem ipsum dolor sit amet, consectetur adipiscing elit, sed do eiusmod tempor incididunt ut labore et dolore magna aliqua. Ut enim ad minim veniam, quis nostrud exercitation ullamco laboris nisi ut aliquip ex ea commodo consequat.</p>
  </div>

  <div class="svc" style="left:561px;top:828px"><svg class="ico" viewBox="0 0 46 46"><circle cx="23" cy="23" r="23" fill="var(--teal)"/><path d="M15 32 L23 12 L31 32 M18 25 H28" fill="none" stroke="#fff" stroke-width="3"/></svg><p>Accommodation / tenancy assistance</p><span class="go"></span></div>
  <div class="svc" style="left:860px;top:828px"><svg class="ico" viewBox="0 0 46 46"><circle cx="23" cy="23" r="23" fill="var(--teal)"/><circle cx="23" cy="23" r="12" fill="none" stroke="#fff" stroke-width="3"/><path d="M14 26 C20 20 26 26 32 20" fill="none" stroke="#fff" stroke-width="3"/></svg><p>Participation in community, social and civic activities</p><span class="go"></span></div>

  <div class="svc" style="left:561px;top:895px"><svg class="ico" viewBox="0 0 46 46"><circle cx="23" cy="23" r="23" fill="var(--teal)"/><path d="M12 14 L22 14 L32 30 L24 34 Z" fill="none" stroke="#fff" stroke-width="3"/></svg><p>Group and centre-based activities</p><span class="go"></span></div>
  <div class="svc" style="left:860px;top:895px"><svg class="ico" viewBox="0 0 46 46"><circle cx="23" cy="23" r="23" fill="var(--teal)"/><path d="M15 32 L23 12 L31 32 M18 25 H28" fill="none" stroke="#fff" stroke-width="3"/></svg><p>Assistance with daily personal activities</p><span class="go"></span></div>

  <div class="svc" style="left:561px;top:963px"><svg class="ico" viewBox="0 0 46 46"><circle cx="23" cy="23" r="23" fill="var(--teal)"/><rect x="14" y="14" width="18" height="18" transform="rotate(45 23 23)" fill="none" stroke="#fff" stroke-width="3"/><path d="M17 23 H29 M23 17 V29" stroke="#fff" stroke-width="2"/></svg><p>Assistance in coordinating or managing life stages, transitions and supports</p><span class="go"></span></div>
  <div class="svc" style="left:860px;top:963px"><svg class="ico" viewBox="0 0 46 46"><circle cx="23" cy="23" r="23" fill="var(--teal)"/><path d="M15 14 V28 C15 34 31 34 31 28 V14" fill="none" stroke="#fff" stroke-width="3"/><path d="M23 16 V32" stroke="#fff" stroke-width="3"/></svg><p>Innovative community participation</p><span class="go"></span></div>

  <div class="svc" style="left:561px;top:1030px"><svg class="ico" viewBox="0 0 46 46"><circle cx="23" cy="23" r="23" fill="var(--teal)"/><path d="M15 32 L23 12 L31 32 M18 25 H28" fill="none" stroke="#fff" stroke-width="3"/></svg><p>Community nursing care</p><span class="go"></span></div>
  <div class="svc" style="left:860px;top:1030px"><svg class="ico" viewBox="0 0 46 46"><circle cx="23" cy="23" r="23" fill="var(--teal)"/><path d="M12 14 L22 14 L32 30 L24 34 Z" fill="none" stroke="#fff" stroke-width="3"/></svg><p>Therapeutic supports</p><span class="go"></span></div>

  <div class="svc" style="left:561px;top:1097px"><svg class="ico" viewBox="0 0 46 46"><circle cx="23" cy="23" r="23" fill="var(--teal)"/><path d="M15 14 V28 C15 34 31 34 31 28 V14" fill="none" stroke="#fff" stroke-width="3"/><path d="M23 16 V32" stroke="#fff" stroke-width="3"/></svg><p>Development of daily care and life skills</p><span class="go"></span></div>
  <div class="svc" style="left:860px;top:1097px"><svg class="ico" viewBox="0 0 46 46"><circle cx="23" cy="23" r="23" fill="var(--teal)"/><path d="M15 32 L23 12 L31 32 M18 25 H28" fill="none" stroke="#fff" stroke-width="3"/></svg><p>Assistance with travel/ transport arrangements</p><span class="go"></span></div>

  <div class="svc" style="left:561px;top:1165px"><svg class="ico" viewBox="0 0 46 46"><circle cx="23" cy="23" r="23" fill="var(--teal)"/><path d="M12 14 L22 14 L32 30 L24 34 Z" fill="none" stroke="#fff" stroke-width="3"/></svg><p>Assistance with daily life tasks in a group or shared living arrangement</p><span class="go"></span></div>
  <div class="svc" style="left:860px;top:1165px"><svg class="ico" viewBox="0 0 46 46"><circle cx="23" cy="23" r="23" fill="var(--teal)"/><rect x="14" y="14" width="18" height="18" transform="rotate(45 23 23)" fill="none" stroke="#fff" stroke-width="3"/><path d="M17 23 H29 M23 17 V29" stroke="#fff" stroke-width="2"/></svg><p>Specialist Disability Accommodation</p><span class="go"></span></div>

  <div class="svc" style="left:561px;top:1232px"><svg class="ico" viewBox="0 0 46 46"><circle cx="23" cy="23" r="23" fill="var(--teal)"/><path d="M15 32 L23 12 L31 32 M18 25 H28" fill="none" stroke="#fff" stroke-width="3"/></svg><p>Accommodation / tenancy assistance</p><span class="go"></span></div>
  <div class="svc" style="left:860px;top:1232px"><svg class="ico" viewBox="0 0 46 46"><circle cx="23" cy="23" r="23" fill="var(--teal)"/><path d="M15 14 V28 C15 34 31 34 31 28 V14" fill="none" stroke="#fff" stroke-width="3"/><path d="M23 16 V32" stroke="#fff" stroke-width="3"/></svg><p>Household tasks</p><span class="go"></span></div>
</section>

<h2 class="section-title" style="top:1355px">Our Vacancies</h2>

<section class="vacancy-panel">
  <h2>SDA in Jordan Springs</h2>
  <p class="lead">Lorem ipsum dolor sit amet, consectetur adipiscing elit, sed do eiusmod tempor incididunt ut labore et dolore magna aliqua. Ut enim ad minim veniam, quis nostrud exercitation ullamco laboris nisi ut aliquip ex ea commodo consequat.</p>

  <div class="amenity" style="left:37px;top:207px"><svg viewBox="0 0 56 56" fill="none" stroke="var(--teal)" stroke-width="3"><rect x="4" y="8" width="48" height="20" rx="3"/><path d="M10 22 H46 M14 34 L10 46 M22 34 V48 M34 34 V48 M42 34 L46 46" stroke-dasharray="3 3"/></svg>Ducated air<br>conditioning</div>
  <div class="amenity" style="left:236px;top:207px"><svg viewBox="0 0 56 56" fill="none" stroke="var(--teal)" stroke-width="3"><rect x="4" y="4" width="48" height="48" rx="4"/><circle cx="26" cy="14" r="4"/><path d="M26 20 V32 H36 L40 42 M20 28 A10 10 0 1 0 32 40"/></svg>Disabilty access<br>walkways</div>
  <div class="amenity" style="left:419px;top:207px"><svg viewBox="0 0 56 56" fill="none" stroke="var(--teal)" stroke-width="3"><rect x="4" y="4" width="48" height="38" rx="2"/><circle cx="28" cy="18" r="7" fill="var(--teal)"/><path d="M14 42 C14 30 42 30 42 42 Z" fill="var(--teal)"/><path d="M18 50 H38"/></svg>24/7 intercom</div>

  <div class="amenity" style="left:37px;top:297px"><svg viewBox="0 0 56 56" fill="none" stroke="var(--teal)" stroke-width="3"><rect x="10" y="4" width="36" height="48" rx="2"/><rect x="18" y="12" width="12" height="10"/><path d="M10 32 H46 M24 40 H34"/></svg>Ovens with side<br>hinged doors</div>
  <div class="amenity" style="left:236px;top:297px"><svg viewBox="0 0 56 56" fill="none" stroke="var(--teal)" stroke-width="3"><path d="M4 24 H52 C52 38 42 44 28 44 C14 44 4 38 4 24 Z M20 44 V52 H36 V44 M28 6 V16 M20 10 L24 16 M36 10 L32 16"/></svg>Accessible was<br>basins</div>
  <div class="amenity" style="left:419px;top:297px"><svg viewBox="0 0 56 56" fill="none" stroke="var(--teal)" stroke-width="3"><rect x="4" y="10" width="48" height="36" rx="2"/><path d="M14 36 L40 18 M14 36 H10"/></svg>Celling hoist</div>

  <div class="amenity" style="left:37px;top:387px"><svg viewBox="0 0 56 56" fill="none" stroke="var(--teal)" stroke-width="3"><rect x="4" y="6" width="48" height="44" rx="3"/><rect x="12" y="18" width="32" height="24"/><path d="M12 12 H16 M22 12 H26 M32 12 H36"/></svg>Hight adjustable<br>bench and cook<br>taps</div>
  <div class="amenity" style="left:236px;top:387px"><svg viewBox="0 0 56 56" fill="none" stroke="var(--teal)" stroke-width="3"><rect x="6" y="6" width="44" height="44"/><path d="M28 6 V50 M20 28 L24 24 V32 Z M36 28 L32 24 V32 Z" fill="var(--teal)"/></svg>Automated/security<br>activated doors</div>
  <div class="amenity" style="left:419px;top:387px"><svg viewBox="0 0 56 56" fill="none" stroke="var(--teal)" stroke-width="4"><path d="M6 22 C18 10 38 10 50 22 M13 30 C22 22 34 22 43 30 M20 38 C25 34 31 34 36 38"/><circle cx="28" cy="46" r="3" fill="var(--teal)"/></svg>Wifi internet</div>

  <div class="amenity" style="left:30px;top:480px"><svg viewBox="0 0 56 56" fill="var(--teal)"><path d="M34 4 L52 22 L40 34 L22 16 Z M22 28 L28 34 L10 52 L4 46 Z"/></svg>Uninterrupted<br>power suplay (UPS)</div>

  <p class="lifestyle-label">Comes with the lifestyle</p>
  <div class="amenity" style="left:25px;top:656px"><svg viewBox="0 0 56 56" fill="var(--teal)"><rect x="6" y="4" width="30" height="40" rx="6"/><rect x="30" y="30" width="24" height="16" rx="4"/><circle cx="14" cy="48" r="4"/><circle cx="46" cy="50" r="4"/></svg>Public transport<br>nearby</div>
  <div class="amenity" style="left:224px;top:656px"><svg viewBox="0 0 56 56" fill="none" stroke="var(--teal)" stroke-width="3"><path d="M6 22 H50 C50 32 40 38 28 38 C16 38 6 32 6 22 Z" fill="var(--teal)"/><path d="M20 38 L14 52 M36 38 L42 52 M18 4 C14 10 22 12 18 18 M28 4 C24 10 32 12 28 18 M38 4 C34 10 42 12 38 18"/></svg>Communal rooftop<br>bbq</div>
  <div class="amenity" style="left:421px;top:656px"><svg viewBox="0 0 56 56" fill="none" stroke="var(--teal)" stroke-width="3"><rect x="6" y="10" width="44" height="40" rx="3"/><path d="M28 20 V40 M18 30 H38" stroke-width="5"/></svg>Pharmacies and<br>medical services<br>nearby</div>
  <div class="amenity" style="left:25px;top:758px"><svg viewBox="0 0 56 56" fill="var(--teal)"><path d="M10 12 H42 L38 52 H14 Z"/><rect x="8" y="6" width="36" height="6"/><path d="M44 18 H50 V30 H42" fill="none" stroke="var(--teal)" stroke-width="3"/></svg>Cafes and shops<br>nearby</div>
  <div class="amenity" style="left:210px;top:758px"><svg viewBox="0 0 56 56" fill="var(--teal)"><path d="M4 40 L10 28 H32 L38 40 V48 H4 Z"/><ellipse cx="44" cy="18" rx="10" ry="14"/><rect x="42" y="28" width="4" height="22"/></svg>&nbsp;&nbsp;Parking available</div>

  <form class="enquiry-card">
    <div class="field" style="left:23px;top:34px;width:210px">First name</div>
    <div class="field" style="left:245px;top:34px;width:210px">Last name</div>
    <div class="field" style="left:23px;top:105px;width:432px">Email</div>
    <div class="field" style="left:23px;top:175px;width:432px">Support Coordinator<span class="chev"></span></div>
    <div class="field" style="left:23px;top:246px;width:432px">NSW<span class="chev"></span></div>
    <div class="field" style="left:23px;top:318px;width:432px">Poscode</div>
    <div class="field" style="left:23px;top:389px;width:432px">Phone</div>
    <div class="btn-teal" style="left:272px;top:467px;width:183px;height:54px;line-height:54px;font-size:24px">Enquire Now</div>
    <div class="reach">Reach out to our team</div>
    <div class="contact-line" style="top:586px"><svg viewBox="0 0 26 26"><rect width="26" height="26" rx="5" fill="var(--teal)"/><path d="M8 6 L11 6 L12 10 L10 11 C11 14 12 15 15 16 L16 14 L20 15 L20 18 C14 19 7 12 8 6 Z" fill="#fff"/></svg>+61 0400 318 562</div>
    <div class="contact-line" style="top:620px"><svg viewBox="0 0 26 26"><rect x="1" y="5" width="24" height="17" fill="var(--teal)"/><path d="M1 5 L13 15 L25 5" fill="none" stroke="#fff" stroke-width="2"/></svg>info@tallowcrestcare.com.au</div>
  </form>

  <p class="next-steps">Next steps<br>If you would like to apply or collect more information, you can speak to our team by phone on <u>+61 0400 318 562 </u>or by <u>email at info@tallowcrestcare.com.au.</u><br><br><u>Looking</u> for more options? Browse more <u>SDA homes in Sydney.</u></p>
</section>

<section class="listings">
  <h2>View our SDA vacancies and homes being built</h2>
  <p class="sub">The following are our SDA vacancies and buildings that are being built around you</p>
  <div class="filter">
    <label style="left:12px">Current or Future</label>
    <label style="left:168px">Design Category</label>
    <label style="left:321px">Location</label>
    <div class="select" style="left:12px;width:139px">Both</div>
    <div class="select" style="left:167px;width:140px">All Categories</div>
    <div class="select" style="left:321px;width:139px">All Categories</div>
    <div class="search-btn"><svg viewBox="0 0 41 41" width="41" height="41"><circle cx="18" cy="18" r="9" fill="none" stroke="#fff" stroke-width="3.5"/><path d="M25 25 L32 32" stroke="#fff" stroke-width="4"/></svg></div>
  </div>

  <article class="prop" style="left:21px">
    <div class="pic" role="img" aria-label="Photo of a multi-storey white apartment building" style="background:linear-gradient(180deg,#8fb3d9,#e8ecef 55%,#6f7d6a)"></div>
    <h3>Specialist Disability Accommodation Liverpool, Wattlebank St</h3>
    <p>Lorem ipsum dolor sit amet, consectetur adipiscing elit, sed do eiusmod tempor incididunt</p>
    <div class="meta"><span><b></b>Strategic location</span><span><b></b>Near hospital</span><span><b></b>spacious building</span><span><b></b>Near school</span></div>
    <div class="stats"><span><b></b>2</span><span><b></b></span><span><b></b>3</span></div>
  </article>
  <article class="prop" style="left:233px">
    <div class="pic" role="img" aria-label="Photo of a rooftop terrace with outdoor seating" style="background:linear-gradient(180deg,#c7ccd0,#7d8a86 60%,#4e5550)"></div>
    <h3>Specialist Disability Accommodation Liverpool, Wattlebank St</h3>
    <p>Lorem ipsum dolor sit amet, consectetur adipiscing elit, sed do eiusmod tempor incididunt</p>
    <div class="meta"><span><b></b>Strategic location</span><span><b></b>Near hospital</span><span><b></b>spacious building</span><span><b></b>Near school</span></div>
    <div class="stats"><span><b></b>2</span><span><b></b></span><span><b></b>3</span></div>
  </article>
  <article class="prop" style="left:446px">
    <div class="pic" role="img" aria-label="Photo of a modern house with timber cladding" style="background:linear-gradient(180deg,#a9c4dc,#b98a5a 55%,#5d4a3a)"></div>
    <h3>Specialist Disability Accommodation Liverpool, Wattlebank St</h3>
    <p>Lorem ipsum dolor sit amet, consectetur adipiscing elit, sed do eiusmod tempor incididunt</p>
    <div class="meta"><span><b></b>Strategic location</span><span><b></b>Near hospital</span><span><b></b>spacious building</span><span><b></b>Near school</span></div>
    <div class="stats"><span><b></b>2</span><span><b></b></span><span><b></b>3</span></div>
  </article>

  <div class="map" role="img" aria-label="Map of Greater Western Sydney showing property locations" style="background:linear-gradient(135deg,#dfe8d8,#eef0ea 45%,#d6e2ea)"></div>

  <div class="pager"><span class="arrow"></span><span class="dim">1</span><span>2</span><span>3</span><span>4</span><span>5</span><span>6</span><span class="arrow"></span></div>
</section>

<section class="help">
  <div class="abs" role="img" aria-label="Photo of a smiling customer support agent wearing a headset" style="left:31px;top:2925px;width:632px;height:264px;background:linear-gradient(90deg,#eef0f2,#d8dde2 40%,#b9a79a 70%,#ece9e6)"></div>
  <h2>Tallowcrest Care is here to help</h2>
  <p>If you have any questions, concerns or are having trouble finding an answer to a question, please do not hesitate to contact us using the form below, Alternatively you can use the contact details in the “How to reach us” section of this page.</p>
  <form class="help-form">
    <div class="field" style="left:24px;top:33px;width:209px">Last name</div>
    <div class="field" style="left:245px;top:33px;width:209px">Last name</div>
    <div class="field" style="left:24px;top:104px;width:209px">Email</div>
    <div class="field" style="left:245px;top:104px;width:209px">Phone</div>
    <div class="field small" style="left:24px;top:175px;width:209px">How did you hear about Tallowcrest Care?</div>
    <div class="field small" style="left:245px;top:175px;width:209px">What is the best time for Tallowcrest Care to contact you?</div>
    <div class="field" style="left:24px;top:246px;width:430px;height:110px;line-height:1;padding-top:14px">Message</div>
    <div class="btn-teal" style="left:329px;top:386px;width:125px;height:54px;line-height:54px;font-size:24px">Send</div>
  </form>
</section>

<footer class="site-footer">
  <div class="footer-tab">
    <div class="item" style="left:35px">Address<br>New South Wales, Australia</div>
    <svg class="abs" style="left:203px;top:5px" width="24" height="32" viewBox="0 0 24 32"><path d="M12 30 C4 20 2 16 2 11 A10 10 0 0 1 22 11 C22 16 20 20 12 30 Z" fill="none" stroke="var(--teal)" stroke-width="2"/><circle cx="12" cy="11" r="4" fill="none" stroke="var(--teal)" stroke-width="2"/></svg>
    <div class="item" style="left:275px">Phone<br>+61 0400 318 562</div>
    <svg class="abs" style="left:392px;top:4px" width="34" height="34" viewBox="0 0 34 34"><rect x="1" y="1" width="32" height="32" rx="8" fill="none" stroke="var(--teal)" stroke-width="2"/><path d="M10 8 L14 8 L15 13 L13 14 C14 18 16 20 20 21 L21 19 L26 20 L26 24 C18 25 9 16 10 8 Z" fill="none" stroke="var(--teal)" stroke-width="2"/></svg>
  </div>
  <div class="footer-brand"><i></i>Tallowcrest Care</div>
  <div class="socials"><span></span><span></span><span></span><span></span><span></span></div>
  <div class="foot-col" style="left:266px">
    <h4>ACCOMMODATION</h4>
    <ul><li><a href="#"><u>Supported Independent Living (SIL)</u></a></li><li><a href="#"><u>Specialist Disability Accommodation (SDA)</u></a></li><li><a href="#"><u>Short term Accommodation (Respite)</u></a></li><li>Vacancies</li></ul>
  </div>
  <div class="foot-col" style="left:552px">
    <h4>WHAT WE DO</h4>
    <ul><li>In Home Care</li><li>Social &amp; Community Services</li><li>Therapeutic Supports</li><li>Support Coordination</li><li>Home Modifications</li></ul>
  </div>
  <div class="sub-title">Subscribe for Newsletter</div>
  <div class="sub-input">Enter your email</div>
  <div class="sub-btn">Subscribe</div>
  <div class="copyright">Copyright 2024 © All Right Reserved</div>
  <div class="legal"><span>· Privacy Policy</span><span>- Terms &amp; Conditions</span><span>- Disclaimer</span><span>- Support</span><span>- FAQ</span></div>
</footer>

</div>
</body>
</html>
```